Dental Office Needs Exciting New Stationary

We need a stationary design that incorporates the logo that we already have and would like to keep the existing color scheme. We need something clean and professional. This is a Endodontic (root canals) office and must represent a dental specialist's office. I need a design for a business card, envelope, and letterhead that all coordinate. I would like the business card to incorporate the information in the business card sample that I am providing. I made the business card design myself but would like to see a better one.
Dental

```html
<!DOCTYPE html>
<html lang="en">
<head>
<meta charset="utf-8">
<title>Summit Endodontics Letterhead</title>
<link rel="stylesheet" href="https://fonts.googleapis.com/css2?family=Exo+2:ital,wght@0,300;0,400;0,500;0,600;1,400&display=swap">
<style>
  :root {
    --backdrop: #e9ecf1;
    --paper: #f7f7f8;
    --brand-blue: #1b5aa6;
    --brand-grey: #9aa0aa;
    --ink: #55575f;
    --ink-dark: #2d2f35;
    --signature-tone: #c9cdd6;
  }
  * { box-sizing: border-box; margin: 0; padding: 0; }
  html, body {
    width: 1200px; height: 1000px; overflow: hidden;
    background: var(--backdrop);
    font-family: "Exo 2", sans-serif;
  }
  .letterhead {
    position: absolute; left: 271px; top: 30px;
    width: 657px; height: 940px;
    background: var(--paper);
    box-shadow: 0 2px 10px rgba(40, 50, 70, 0.12);
  }
  .brand {
    position: absolute; left: 121px; top: 128px;
    display: flex; align-items: center; gap: 10px;
  }
  .brand-dot {
    width: 16px; height: 16px; border-radius: 50%;
    background: var(--brand-blue);
  }
  .brand-name {
    font-weight: 600; font-size: 20px; letter-spacing: 0.5px;
    color: var(--brand-blue); text-transform: uppercase;
  }
  .contact {
    position: absolute; left: 397px; top: 132px;
    display: flex; gap: 18px;
    font-size: 6.5px; line-height: 9px; color: var(--ink);
  }
  .contact-column { display: flex; flex-direction: column; }
  .contact-line { display: flex; align-items: center; gap: 3px; }
  .contact-line.indented { padding-left: 9px; }
  .contact-icon { width: 6px; height: 6px; fill: var(--brand-blue); }
  .salutation {
    position: absolute; left: 121px; top: 246px;
    font-style: italic; font-size: 13px; color: var(--ink-dark);
  }
  .letter-body {
    position: absolute; left: 121px; top: 288px; width: 436px;
    font-size: 9.4px; line-height: 13.7px; font-weight: 300;
    color: var(--ink); text-align: justify;
  }
  .letter-body p + p { margin-top: 21px; }
  .closing {
    position: absolute; right: 120px; top: 678px;
    font-style: italic; font-size: 12px; color: var(--ink-dark);
  }
  .signature {
    position: absolute; left: 322px; top: 712px;
    width: 160px; height: 32px; border-radius: 4px;
    background: linear-gradient(90deg, var(--signature-tone), rgba(201, 205, 214, 0.3));
  }
</style>
</head>
<body>
  <main class="letterhead">
    <header class="brand">
      <span class="brand-dot"></span>
      <span class="brand-name">Summit Endodontics</span>
    </header>

    <address class="contact">
      <div class="contact-column">
        <span class="contact-line"><svg class="contact-icon" viewBox="0 0 10 10"><path d="M5 0a3.5 3.5 0 0 0-3.5 3.5C1.5 6 5 10 5 10s3.5-4 3.5-6.5A3.5 3.5 0 0 0 5 0z"/></svg>1420 Elm Street,</span>
        <span class="contact-line indented">Riverton, CA 95001</span>
        <span class="contact-line"><svg class="contact-icon" viewBox="0 0 10 10"><path d="M2 0l2 2.5-1 1.5a6 6 0 0 0 3 3l1.5-1L10 8l-1.5 2C4 10 0 6 0 1.5z"/></svg>916.555.0142</span>
        <span class="contact-line"><svg class="contact-icon" viewBox="0 0 10 10"><rect x="0" y="3" width="10" height="6" rx="1"/><rect x="2" y="0" width="6" height="3"/></svg>916.555.0143</span>
      </div>
      <div class="contact-column">
        <span class="contact-line"><svg class="contact-icon" viewBox="0 0 10 10"><path d="M5 0a3.5 3.5 0 0 0-3.5 3.5C1.5 6 5 10 5 10s3.5-4 3.5-6.5A3.5 3.5 0 0 0 5 0z"/></svg>3800 Oak Av. Suite 2,</span>
        <span class="contact-line indented">Fairview, CA 95002</span>
        <span class="contact-line"><svg class="contact-icon" viewBox="0 0 10 10"><path d="M2 0l2 2.5-1 1.5a6 6 0 0 0 3 3l1.5-1L10 8l-1.5 2C4 10 0 6 0 1.5z"/></svg>916.555.0187</span>
        <span class="contact-line"><svg class="contact-icon" viewBox="0 0 10 10"><rect x="0" y="3" width="10" height="6" rx="1"/><rect x="2" y="0" width="6" height="3"/></svg>916.555.0188</span>
      </div>
    </address>

    <p class="salutation">Dear&nbsp; Client,</p>

    <section class="letter-body">
      <p>Lorem ipsum dolor sit amet, consectetur adipiscing elit. Nulla sodales nisi vitae Lorem ipsum dolor sit amet, consectetur adipiscing elit. Suspendisse feugiat eros nisl, a facilisis risus eleifend sed. Aliquam mauris enim, fermentum eu lacinia sit amet, laoreet eu leo. Nullam eleifend nulla in libero tristique, ac vulputate odio tincidunt. Etiam non condimentum tortor. Integer suscipit neque nec odio porttitor cursus. Phasellus a sapien blandit, suscipit justo id, condimentum ante. Morbi tristique justo risus, id mattis dui molestie ut. Nullam volutpat ut quam commodo faucibus. Pellentesque urna est, interdum in elit quis, pharetra elementum orci. Nam pharetra velit molestie justo placerat scelerisque.</p>
      <p>Sed est tellus, rutrum in nisl a, consequat sollicitudin elit. Aliquam vitae vestibulum felis. Morbi iaculis nunc volutpat diam ullamcorper vestibulum. Nulla facilisi. Aenean accumsan gravida orci, vitae consectetur justo aliquet et. Curabitur vehicula tempus dolor, a gravida metus vestibulum sit amet. Integer non erat elementum, malesuada metus vel, fermentum lectus. Etiam sit amet nisl ac augue semper ultrices.</p>
      <p>Nulla tincidunt molestie libero vel pretium. Donec condimentum nulla sit amet risus semper imperdiet. Duis congue eros nec diam blandit, et pellentesque sapien auctor. Curabitur iaculis enim lectus, in imperdiet mauris mattis eget. Etiam ac ornare metus. Mauris risus leo, egestas at dolor a, ultrices adipiscing est. Nunc faucibus scelerisque mollis. Pellentesque aliquet mauris tellus, id dignissim risus viverra et. Mauris venenatis lobortis eros. Nam id diam in ligula malesuada feugiat. Cras turpis felis, aliquet id mauris elementum, feugiat ultricies nisl.</p>
    </section>

    <p class="closing">Best regards.</p>
    <div class="signature" role="img" aria-label="Handwritten signature of Daniel Reyes"></div>
  </main>
</body>
</html>
```